Corvane Capital Business Cards

These are professional business cards that are for my family office.
Put fake emails and phone numbers as of now until I finalize those components. This family office controls my families investments, assets, and future. The cards should be professional.
..
.
.
.
I just uploaded another variation of a logo I would like to see as a business card to I am inbeteen which logo to use

Target Market(s)

business

Industry/Entity Type

business

Contact Information for Business Card

Professional, wealth related, finance related.

Requirements
Must have
• Logo

```html
<!DOCTYPE html>
<html lang="en">
<head>
<meta charset="utf-8">
<title>Corvane Capital Business Cards</title>
<link rel="stylesheet" href="https://fonts.googleapis.com/css2?family=Cinzel:wght@500&family=Montserrat:wght@400;500&display=swap">
<style>
  :root {
    --navy: #161d2b;
    --navy-deep: #0f1520;
    --navy-soft: #26334a;
    --paper: #ffffff;
    --ink: #161d2b;
    --muted: #555b66;
    --rule: #b5b8bd;
    --backdrop: #e6e7ea;
  }
  * { box-sizing: border-box; margin: 0; padding: 0; }
  html, body { width: 1200px; height: 915px; overflow: hidden; }
  body {
    background: var(--backdrop);
    display: flex;
    flex-direction: column;
    align-items: center;
    justify-content: center;
    gap: 30px;
  }
  .card {
    width: 720px;
    height: 411px;
    border-radius: 26px;
    position: relative;
    overflow: hidden;
    box-shadow: 0 6px 18px rgba(0,0,0,.12);
  }
  .card-front { background: var(--navy); }
  .front-pattern {
    position: absolute; inset: 0;
    background: linear-gradient(200deg, var(--navy-soft) 0%, var(--navy) 45%, var(--navy-deep) 100%);
  }
  .front-brand {
    position: absolute;
    right: 78px; top: 50%;
    transform: translateY(-50%);
    display: flex; align-items: center; gap: 14px;
  }
  .front-brand-circle {
    width: 46px; height: 46px;
    border: 2px solid var(--paper);
    border-radius: 50%;
  }
  .front-brand-name {
    font-family: "Cinzel", serif;
    font-weight: 500;
    font-size: 22px;
    color: var(--paper);
    letter-spacing: 1px;
  }
  .card-back { background: var(--paper); }
  .company-name {
    position: absolute;
    top: 92px; left: 0; right: 0;
    text-align: center;
    font-family: "Cinzel", serif;
    font-weight: 500;
    font-size: 46px;
    color: var(--ink);
    letter-spacing: 1px;
  }
  .details {
    position: absolute;
    top: 178px; left: 0; right: 0;
    display: flex; justify-content: center; align-items: center;
  }
  .person { text-align: right; padding-right: 26px; }
  .person-name {
    font-family: "Cinzel", serif;
    font-weight: 500;
    font-size: 25px;
    color: var(--ink);
  }
  .person-title {
    font-family: "Montserrat", sans-serif;
    font-size: 15px;
    color: var(--muted);
    margin-top: 2px;
  }
  .divider { width: 1px; height: 96px; background: var(--rule); }
  .contact-list {
    list-style: none;
    padding-left: 26px;
    font-family: "Montserrat", sans-serif;
    font-size: 15px;
    color: var(--muted);
  }
  .contact-list li {
    display: flex; align-items: center; gap: 9px;
    line-height: 29px;
  }
  .contact-list svg { width: 13px; height: 13px; fill: var(--ink); flex: none; }
  .address-band {
    position: absolute;
    left: 0; right: 0; top: 320px;
    height: 44px;
    background: var(--navy);
    display: flex; align-items: center; justify-content: center;
    font-family: "Montserrat", sans-serif;
    font-weight: 500;
    font-size: 15px;
    color: var(--paper);
    letter-spacing: .3px;
  }
</style>
</head>
<body>

  <section class="card card-front">
    <div class="front-pattern" role="img" aria-label="Repeating brand mark pattern in tonal navy with a soft blue sheen"></div>
    <div class="front-brand">
      <span class="front-brand-circle"></span>
      <span class="front-brand-name">Corvane Capital</span>
    </div>
  </section>

  <section class="card card-back">
    <h1 class="company-name">Corvane Capital</h1>
    <div class="details">
      <div class="person">
        <p class="person-name">Elena Marsh</p>
        <p class="person-title">CEO/Founder</p>
      </div>
      <div class="divider"></div>
      <ul class="contact-list">
        <li>
          <svg viewBox="0 0 16 16" aria-hidden="true"><path d="M3 1h3l1.5 4-2 1.3a9 9 0 0 0 4.2 4.2L11 8.5l4 1.5v3a2 2 0 0 1-2 2A12 12 0 0 1 1 3a2 2 0 0 1 2-2z"/></svg>
          (555) 010-4417
        </li>
        <li>
          <svg viewBox="0 0 16 16" aria-hidden="true"><path d="M1 3h14v10H1z M2 4.2v.4l6 4.2 6-4.2v-.4z" fill-rule="evenodd"/></svg>
          ElenaM@corvanecapital.com
        </li>
        <li>
          <svg viewBox="0 0 16 16" aria-hidden="true"><circle cx="8" cy="8" r="7"/><path d="M1 8h14M8 1c2.5 2 2.5 12 0 14M8 1c-2.5 2-2.5 12 0 14" stroke="#fff" stroke-width="1" fill="none"/></svg>
          www.corvanecapital.com
        </li>
      </ul>
    </div>
    <div class="address-band">4820 Linden Ridge Rd Suite 200 Harlow, NM 874105</div>
  </section>

</body>
</html>
```